Cozy Cradle Loops Needs a Beautiful Website

I need a new website for this new E-commerce. I sell handmade baby crochets, e.g. booties, headbands, hats, etc. I need a feminine and soft design to make the moms-to-be say 'oohh ahh'. I'd like pink, blue and gray. I'd like an inviting homepage, and nice regular pages where people can see and order the products.

Industry/Entity Type

Baby

Requirements
Must have
• beautiful, soft, feminine design. Please use pictures of the colors I'd like: brown, yellow, pink and blue. Any combination, but definitely include brown.

```html
<!DOCTYPE html>
<html lang="en">
<head>
<meta charset="utf-8">
<title>Cozy Cradle Loops</title>
<link rel="stylesheet" href="https://fonts.googleapis.com/css2?family=Roboto:wght@400;500;700&family=Roboto+Slab:wght@400;700&display=swap">
<style>
:root{
  --page:#efd3bf;
  --header:#f2d8c6;
  --sheet:#f8e7db;
  --pink:#f8a3ad;
  --pink-deep:#f5728a;
  --cyan:#a9e3e8;
  --cyan-deep:#6fd2dc;
  --brown:#8e5c3b;
  --brown-dark:#7b4e31;
  --tab:#c99170;
  --text:#8a7a72;
  --muted:#a59890;
  --white:#ffffff;
}
*{box-sizing:border-box;margin:0;padding:0}
html,body{width:723px;height:1200px;overflow:hidden}
body{position:relative;background:var(--page);font-family:"Roboto",sans-serif;color:var(--text)}
.abs{position:absolute}
.site-header{left:0;top:0;width:723px;height:108px;background:var(--header);box-shadow:0 2px 4px rgba(150,100,70,.25);z-index:2}
.search{left:325px;top:5px;width:180px;height:12px;background:#f9eee6;border:1px solid #e4cbb9;font-size:5.5px;color:var(--muted);padding:2px 4px;letter-spacing:.5px}
.search svg{position:absolute;right:4px;top:2px}
.signin{left:513px;top:7px;font-size:6px;color:var(--text);letter-spacing:.5px}
.cart-tab{left:547px;top:0;width:90px;height:38px;background:var(--tab);border-radius:0 0 4px 4px;color:var(--white);font-size:6px;text-align:center;letter-spacing:.3px}
.cart-tab svg{position:absolute;left:32px;top:4px}
.cart-tab span{position:absolute;left:0;right:0;top:27px}
.brand{left:95px;top:36px;display:flex;align-items:center;gap:5px;font-family:"Roboto Slab",serif;font-weight:700;font-size:15px;color:var(--pink-deep)}
.brand i{display:block;width:10px;height:10px;border-radius:50%;background:var(--pink-deep)}
.nav a{position:absolute;top:56px;font-size:8px;letter-spacing:1.3px;color:#a08a7e;text-decoration:none}
.nav a.active{color:#7b6a60}
.nav a.active::after{content:"";position:absolute;left:0;right:0;top:12px;height:2px;background:var(--tab)}
.sheet{left:40px;top:108px;width:643px;height:920px;background:var(--sheet)}
.hero{left:89px;top:80px;width:546px;height:242px;background:linear-gradient(90deg,#ddd6cf 0%,#d8cfc7 45%,#c7b5a6 80%,#b99f8e 100%);border:1px solid #fff;z-index:3}
.hero-title{left:73px;top:68px;font-size:31px;font-weight:500;letter-spacing:4px;color:var(--pink);line-height:33px;text-align:center;width:130px}
.hero-sub{left:37px;top:133px;font-size:13.5px;font-weight:700;letter-spacing:1.2px;color:var(--white);white-space:nowrap}
.hero-btn{left:67px;top:156px;width:97px;height:22px;background:var(--pink);color:var(--white);font-size:11px;font-weight:700;letter-spacing:1px;text-align:center;line-height:22px}
.arrow{top:201px;width:18px;height:18px;border-radius:50%;background:rgba(255,255,255,.6);z-index:4}
.arrow svg{position:absolute;left:5px;top:4px}
.tile{top:336px;width:176px;height:116px;overflow:hidden}
.tile-band{left:0;right:0;bottom:0;height:35px;background:rgba(60,50,60,.45);color:var(--white);font-size:10.5px;letter-spacing:1.5px;text-align:center;line-height:38px}
.ship{color:var(--white);text-align:center;width:100%;top:24px;font-family:"Roboto Slab",serif}
.ship b{display:block;font-weight:400;font-size:21px;letter-spacing:2.5px;line-height:24px}
.ship small{display:block;font-family:"Roboto",sans-serif;font-size:11px;letter-spacing:1px;margin-top:1px}
.panel{background:var(--white)}
.ribbon{height:14px;background:var(--pink);color:var(--white);font-size:6.5px;letter-spacing:.8px;text-align:center;line-height:14px}
.product{width:80px}
.product-name{position:absolute;top:0;width:80px;text-align:center;font-size:5.5px;letter-spacing:.8px;color:var(--pink)}
.product-photo{position:absolute;top:9px;width:80px;height:90px}
.price{position:absolute;top:87px;left:0;width:22px;height:12px;background:var(--pink);color:var(--white);font-size:4.5px;line-height:12px;text-align:center}
.add-cart{position:absolute;top:87px;left:22px;width:58px;height:12px;background:var(--cyan);color:#5f9aa0;font-size:4.5px;line-height:12px;text-align:center;letter-spacing:.3px}
.side-copy{font-size:5.5px;line-height:7px;color:var(--muted);width:104px}
.save-label{font-size:7px;letter-spacing:1px;color:var(--cyan-deep)}
.save-value{font-size:22px;font-weight:500;color:var(--cyan-deep);letter-spacing:1px}
.mini-btn{background:var(--pink-deep);color:var(--white);font-size:4.5px;padding:1px 4px;letter-spacing:.5px}
.site-footer{left:0;top:1058px;width:723px;height:142px;background:var(--brown)}
.footer-base{left:0;top:1180px;width:723px;height:20px;background:var(--brown-dark);font-size:5.5px;color:#e5cbb8;text-align:center;line-height:20px;letter-spacing:.5px}
.f-head{top:1087px;font-size:9px;letter-spacing:1.8px;color:#f2ddcc}
.f-links{top:1105px;font-size:6.3px;line-height:7.4px;color:#f2ddcc;letter-spacing:.6px}
.social{top:1106px;width:13px;height:13px;border-radius:2px}
.email{left:453px;top:1106px;width:151px;height:14px;background:#fbefe6;font-size:6px;color:var(--muted);padding:3px 5px;letter-spacing:.5px}
.send{left:604px;top:1106px;width:30px;height:14px;background:var(--pink-deep);color:var(--white);font-size:6.5px;line-height:14px;text-align:center}
.card{top:1137px;width:26px;height:16px;border-radius:2px;border:1px solid #e8d8cc}
</style>
</head>
<body>
<header class="abs site-header">
  <div class="abs search">Enter a Keyword to Search
    <svg width="7" height="7" viewBox="0 0 10 10"><circle cx="4" cy="4" r="3" fill="none" stroke="#a59890" stroke-width="1.4"/><path d="M6.3 6.3 9 9" stroke="#a59890" stroke-width="1.4"/></svg>
  </div>
  <div class="abs signin">Sign in ▾</div>
  <div class="abs cart-tab">
    <svg width="26" height="20" viewBox="0 0 26 20"><path d="M1 2h4l3 11h13l3-8H7" fill="none" stroke="#fff" stroke-width="1.8" stroke-linejoin="round"/><circle cx="10" cy="17" r="1.7" fill="#fff"/><circle cx="19" cy="17" r="1.7" fill="#fff"/></svg>
    <span>0 item(s) - $0.00</span>
  </div>
  <div class="abs brand"><i></i>Cozy Cradle Loops</div>
  <nav class="nav">
    <a class="active" href="#" style="left:323px">HOME</a>
    <a href="#" style="left:373px">PRODUCT</a>
    <a href="#" style="left:439px">ABOUT</a>
    <a href="#" style="left:493px">PAGES</a>
    <a href="#" style="left:545px">BLOG</a>
    <a href="#" style="left:592px">CONTACT</a>
  </nav>
</header>

<div class="abs sheet"></div>

<section class="abs hero" role="img" aria-label="Sleeping newborn wearing a light blue crochet crown">
  <div class="abs hero-title">NEW ARRIVALS</div>
  <div class="abs hero-sub">GET UP TO 10% OFF</div>
  <div class="abs hero-btn">SHOP NOW!</div>
</section>
<div class="abs arrow" style="left:80px"><svg width="8" height="10" viewBox="0 0 8 10"><path d="M6 1 2 5l4 4" fill="none" stroke="#8a7a72" stroke-width="1.5"/></svg></div>
<div class="abs arrow" style="left:624px"><svg width="8" height="10" viewBox="0 0 8 10"><path d="M2 1l4 4-4 4" fill="none" stroke="#8a7a72" stroke-width="1.5"/></svg></div>

<div class="abs tile" style="left:89px;background:linear-gradient(120deg,#8f7ab8,#b7a6c9 60%,#d9cbc4)" role="img" aria-label="Baby asleep on purple blanket wearing a grey crochet crown">
  <div class="abs tile-band">ON SALE</div>
</div>
<div class="abs tile" style="left:275px;background:linear-gradient(120deg,#c9c2b8,#e5d9cc 55%,#bfa893)" role="img" aria-label="Baby lying down wearing a green crochet hat">
  <div class="abs tile-band">SPECIAL OFFERS</div>
</div>
<div class="abs tile" style="left:462px;width:175px;background:linear-gradient(120deg,#3b2f33,#2a2a30 55%,#3a3a40)" role="img" aria-label="Dark background of crochet baby shoes">
  <div class="abs ship"><b>FREE<br>SHIPPING</b><small>on orders over $99.</small></div>
</div>

<section class="abs panel" style="left:88px;top:469px;width:422px;height:514px">
  <div class="ribbon">FEATURED PRODUCTS</div>
</section>

<!-- product grid -->
<div class="abs product" style="left:102px;top:494px"><div class="product-name">LOREM IPSUM</div><div class="product-photo" style="background:#f27fb0" role="img" aria-label="Pink crochet crown headband"></div><div class="price">$15.99</div><div class="add-cart">Add to cart</div></div>
<div class="abs product" style="left:207px;top:494px"><div class="product-name">LOREM IPSUM</div><div class="product-photo" style="background:#6fd3de" role="img" aria-label="Turquoise crochet crown headband"></div><div class="price">$15.99</div><div class="add-cart">Add to cart</div></div>
<div class="abs product" style="left:312px;top:494px"><div class="product-name">LOREM IPSUM</div><div class="product-photo" style="background:#ea5fc9" role="img" aria-label="Magenta crochet crown headband"></div><div class="price">$15.99</div><div class="add-cart">Add to cart</div></div>
<div class="abs product" style="left:417px;top:494px"><div class="product-name">LOREM IPSUM</div><div class="product-photo" style="background:#e94c7b" role="img" aria-label="Rose crochet crown headband"></div><div class="price">$15.99</div><div class="add-cart">Add to cart</div></div>

<div class="abs product" style="left:102px;top:618px"><div class="product-name">LOREM IPSUM</div><div class="product-photo" style="background:linear-gradient(#4a4a4a,#b9b9b9)" role="img" aria-label="Black crochet baby sneakers"></div><div class="price">$15.99</div><div class="add-cart">Add to cart</div></div>
<div class="abs product" style="left:207px;top:618px"><div class="product-name">LOREM IPSUM</div><div class="product-photo" style="background:linear-gradient(#6a5a4c,#8e7a6a)" role="img" aria-label="Brown crochet baby sneakers"></div><div class="price">$15.99</div><div class="add-cart">Add to cart</div></div>
<div class="abs product" style="left:312px;top:618px"><div class="product-name">LOREM IPSUM</div><div class="product-photo" style="background:linear-gradient(#555a66,#8d8f96)" role="img" aria-label="Navy crochet baby sneakers"></div><div class="price">$15.99</div><div class="add-cart">Add to cart</div></div>
<div class="abs product" style="left:417px;top:618px"><div class="product-name">LOREM IPSUM</div><div class="product-photo" style="background:linear-gradient(#2a2a2a,#c9402c)" role="img" aria-label="Red crochet baby sneakers"></div><div class="price">$15.99</div><div class="add-cart">Add to cart</div></div>

<div class="abs product" style="left:102px;top:742px"><div class="product-name">LOREM IPSUM</div><div class="product-photo" style="background:linear-gradient(#dfe4ea,#ecd6d9)" role="img" aria-label="White and pink crochet booties"></div><div class="price">$15.99</div><div class="add-cart">Add to cart</div></div>
<div class="abs product" style="left:207px;top:742px"><div class="product-name">LOREM IPSUM</div><div class="product-photo" style="background:linear-gradient(#1a1a1a,#5c5452)" role="img" aria-label="White crochet sandals with flower"></div><div class="price">$15.99</div><div class="add-cart">Add to cart</div></div>
<div class="abs product" style="left:312px;top:742px"><div class="product-name">LOREM IPSUM</div><div class="product-photo" style="background:linear-gradient(#3a2f2f,#a8282e)" role="img" aria-label="Red crochet booties"></div><div class="price">$15.99</div><div class="add-cart">Add to cart</div></div>
<div class="abs product" style="left:417px;top:742px"><div class="product-name">LOREM IPSUM</div><div class="product-photo" style="background:linear-gradient(#3a3a3a,#2a9aa8)" role="img" aria-label="Teal crochet booties"></div><div class="price">$15.99</div><div class="add-cart">Add to cart</div></div>

<div class="abs product" style="left:102px;top:867px"><div class="product-name">LOREM IPSUM</div><div class="product-photo" style="background:linear-gradient(#6b6662,#cfc8bc)" role="img" aria-label="Cream crochet booties with pink flower"></div><div class="price">$15.99</div><div class="add-cart">Add to cart</div></div>
<div class="abs product" style="left:207px;top:867px"><div class="product-name">LOREM IPSUM</div><div class="product-photo" style="background:linear-gradient(#5e5a56,#d6cfc3)" role="img" aria-label="Cream crochet booties with flower"></div><div class="price">$14.99</div><div class="add-cart">Add to cart</div></div>
<div class="abs product" style="left:312px;top:867px"><div class="product-name">LOREM IPSUM</div><div class="product-photo" style="background:linear-gradient(#2c2c2e,#6c6c70)" role="img" aria-label="Grey crochet booties with red flower"></div><div class="price">$15.99</div><div class="add-cart">Add to cart</div></div>
<div class="abs product" style="left:417px;top:867px"><div class="product-name">LOREM IPSUM</div><div class="product-photo" style="background:linear-gradient(#2c2c2e,#77777a)" role="img" aria-label="Grey crochet booties with pink flower"></div><div class="price">$14.99</div><div class="add-cart">Add to cart</div></div>

<!-- sidebar -->
<aside class="abs panel" style="left:518px;top:469px;width:119px;height:160px">
  <div class="ribbon" style="margin:0 -2px">BEST SELLERS</div>
  <div class="abs" style="left:9px;top:21px;width:104px;height:100px;background:linear-gradient(135deg,#b8343c,#d7c9bf 50%,#7fb6bf)" role="img" aria-label="Collage of best selling crochet booties"></div>
  <p class="abs side-copy" style="left:9px;top:130px">Lorem ipsum dolor sit amet, consectetur adipisicing elit, sed do eiusmod tempor incididunt ut labore et dolore magna aliqua.</p>
</aside>
<aside class="abs panel" style="left:518px;top:651px;width:119px;height:209px">
  <div class="ribbon" style="margin:0 -2px">WINTER COLLECTIONS</div>
  <div class="abs" style="left:9px;top:20px;width:104px;height:106px;background:linear-gradient(135deg,#4b4d55,#a7a9ad 50%,#3a3d46)" role="img" aria-label="Collage of crochet baby sneakers"></div>
  <div class="abs save-label" style="left:9px;top:131px">SAVE UP TO</div>
  <div class="abs save-value" style="left:8px;top:138px">20%</div>
  <div class="abs mini-btn" style="left:9px;top:164px">SHOP NOW!</div>
  <p class="abs side-copy" style="left:9px;top:178px">Lorem ipsum dolor sit amet, consectetur adipisicing elit, sed do eiusmod tempor incididunt ut labore et dolore magna aliqua.</p>
</aside>
<aside class="abs panel" style="left:518px;top:880px;width:119px;height:103px">
  <div class="ribbon" style="margin:0 -2px">TESTIMONIALS</div>
  <p class="abs side-copy" style="left:9px;top:22px">"Lorem ipsum dolor sit amet, consectetur adipisicing elit, sed do eiusmod tempor incididunt ut labore et dolore magna aliqua."</p>
  <p class="abs side-copy" style="left:9px;top:56px">- Mark Dalton -</p>
</aside>

<footer class="abs site-footer"></footer>
<div class="abs f-head" style="left:89px">BROWSE</div>
<div class="abs f-links" style="left:89px">Home<br>Products<br>Page<br>Blog<br>Contact<br>Login</div>
<div class="abs f-head" style="left:188px">SITE INFO</div>
<div class="abs f-links" style="left:189px">About us<br>Customer Testimonials<br>Shipping Details<br>Privacy<br>Terms &amp; Conditions<br>Subscribe</div>
<div class="abs f-head" style="left:329px">FOLLOW US</div>
<div class="abs social" style="left:330px;background:#3b5b9a"></div>
<div class="abs social" style="left:349px;background:#3aa9dd"></div>
<div class="abs f-head" style="left:453px">GET EMAIL EXCLUSIVES</div>
<div class="abs email">Enter Email Address</div>
<div class="abs send">Send</div>
<div class="abs card" style="left:518px;background:#2f7fc1"></div>
<div class="abs card" style="left:549px;background:#f3e2b5"></div>
<div class="abs card" style="left:580px;background:#cc3b2b"></div>
<div class="abs card" style="left:609px;background:#f4f4f4"></div>
<div class="abs footer-base">Cozy Cradle Loops &nbsp;&nbsp; ©2014. All rights reserved</div>
</body>
</html>
```